Shine Fox Auto Care Business Card

2 side business card design for an auto detailing business

Target Market(s)

Auto detailing

Contact Information for Business Card

Things included

The business name “Shine Fox Auto Care”
Mark Dunrow
(403)271-6094
Carrowmere, Sk

Services offered - complete interior& exterior detail
- paint correction & protection
- ceramic coating
- trim restore
- auto carpet & seat cleaning

Requirements
Must have
• Colours that are in my logo

Services offered

My name Mark Dunrow
403-271-6094
Carrowmere, Sk

Not too sure in what order for these ?
Website. Shinefoxautocare.com
Instagram Shinefoxautocare
Email. Shinefoxautoac@mailvento.com

```html
<!DOCTYPE html>
<html lang="en">
<head>
<meta charset="utf-8">
<title>Shine Fox Auto Care – Business Card</title>
<link href="https://fonts.googleapis.com/css2?family=Arimo:wght@400;700&display=swap" rel="stylesheet">
<style>
  :root {
    --page: #1c1c1e;
    --card: #0b0b0c;
    --card-edge: #151517;
    --red: #b3121a;
    --white: #f2f2f2;
    --silver: #c9c9cc;
    --divider: #3a3a3d;
  }
  * { box-sizing: border-box; margin: 0; padding: 0; }
  html, body {
    width: 1200px; height: 900px; overflow: hidden;
    background: var(--page);
    font-family: "Arimo", Arial, sans-serif;
    color: var(--white);
  }
  .sheet {
    width: 1200px; height: 900px;
    display: flex; flex-direction: column;
    align-items: center; justify-content: center;
    gap: 40px;
  }
  .card {
    width: 700px; height: 400px;
    background: var(--card);
    border-radius: 22px;
    border: 1px solid var(--card-edge);
    position: relative;
    overflow: hidden;
  }

  /* Front: contact side */
  .card--front { display: flex; }
  .brand-panel {
    width: 330px; height: 100%;
    display: flex; flex-direction: column;
    align-items: center; justify-content: center;
    gap: 18px;
  }
  .brand-mark {
    width: 110px; height: 110px; border-radius: 50%;
    border: 9px solid var(--red);
  }
  .brand-name {
    font-weight: 700; font-size: 28px;
    letter-spacing: 2px; text-transform: uppercase;
    color: var(--white); text-align: center; line-height: 1.25;
  }
  .divider {
    width: 1px; height: 300px; align-self: center;
    background: var(--divider);
  }
  .contact-panel {
    flex: 1; padding: 0 30px 0 38px;
    display: flex; flex-direction: column; justify-content: center;
  }
  .owner-name {
    color: var(--red); font-size: 30px; font-weight: 400;
    letter-spacing: 3px; text-transform: uppercase;
    margin-bottom: 22px;
  }
  .contact-list { list-style: none; display: flex; flex-direction: column; gap: 14px; }
  .contact-item { display: flex; align-items: center; gap: 12px; font-size: 17px; white-space: nowrap; }
  .contact-icon { width: 24px; height: 24px; flex: none; }

  /* Back: services side */
  .card--back {
    display: flex; flex-direction: column; align-items: center;
    padding-top: 48px;
  }
  .brand-lockup { display: flex; align-items: center; gap: 22px; }
  .brand-lockup .brand-mark { width: 96px; height: 96px; border: 8px solid var(--white); }
  .brand-lockup .brand-name { color: var(--silver); text-align: left; font-size: 30px; }
  .services-title {
    margin-top: 34px; font-weight: 700; font-size: 22px;
    letter-spacing: 1px; text-transform: uppercase;
  }
  .services-lead { margin-top: 6px; font-size: 14px; letter-spacing: .5px; text-transform: uppercase; }
  .services-cols { margin-top: 26px; display: flex; gap: 60px; }
  .services-list { list-style: none; display: flex; flex-direction: column; gap: 8px; font-size: 17px; }
  .services-list li::before {
    content: ""; display: inline-block; width: 8px; height: 8px;
    border-radius: 50%; background: var(--white);
    margin-right: 8px; vertical-align: middle;
  }
</style>
</head>
<body>
<main class="sheet">

  <section class="card card--front" aria-label="Business card front">
    <div class="brand-panel">
      <div class="brand-mark"></div>
      <p class="brand-name">Shine Fox<br>Auto Care</p>
    </div>
    <div class="divider"></div>
    <div class="contact-panel">
      <h1 class="owner-name">Mark Dunrow</h1>
      <ul class="contact-list">
        <li class="contact-item">
          <svg class="contact-icon" viewBox="0 0 24 24" aria-hidden="true"><circle cx="12" cy="12" r="12" fill="#b3121a"/><path d="M8.5 6.5l2 2-1.2 1.6c.8 1.7 2 2.9 3.6 3.6l1.6-1.2 2 2-1.3 1.8c-4-.6-7.6-4.2-8.2-8.2z" fill="#fff"/></svg>
          <span>(403)271-6094</span>
        </li>
        <li class="contact-item">
          <svg class="contact-icon" viewBox="0 0 24 24" aria-hidden="true"><circle cx="12" cy="12" r="12" fill="#b3121a"/><rect x="6" y="8" width="12" height="8" fill="none" stroke="#fff" stroke-width="1.4"/><path d="M6 8l6 5 6-5" fill="none" stroke="#fff" stroke-width="1.4"/></svg>
          <span>Shinefoxautocare@mailvento.com</span>
        </li>
        <li class="contact-item">
          <svg class="contact-icon" viewBox="0 0 24 24" aria-hidden="true"><circle cx="12" cy="12" r="12" fill="#b3121a"/><circle cx="12" cy="12" r="6" fill="none" stroke="#fff" stroke-width="1.3"/><ellipse cx="12" cy="12" rx="2.6" ry="6" fill="none" stroke="#fff" stroke-width="1.2"/><path d="M6 12h12" stroke="#fff" stroke-width="1.2"/></svg>
          <span>www.Shinefoxautocare.com</span>
        </li>
        <li class="contact-item">
          <svg class="contact-icon" viewBox="0 0 24 24" aria-hidden="true"><circle cx="12" cy="12" r="12" fill="#b3121a"/></svg>
          <span>Shinefoxautocare</span>
        </li>
        <li class="contact-item">
          <svg class="contact-icon" viewBox="0 0 24 24" aria-hidden="true"><circle cx="12" cy="12" r="12" fill="#b3121a"/><path d="M12 5.5a4.5 4.5 0 0 0-4.5 4.5c0 3.4 4.5 8.5 4.5 8.5s4.5-5.1 4.5-8.5A4.5 4.5 0 0 0 12 5.5z" fill="#fff"/><circle cx="12" cy="10" r="1.7" fill="#b3121a"/></svg>
          <span>Carrowmere, Sk</span>
        </li>
      </ul>
    </div>
  </section>

  <section class="card card--back" aria-label="Business card back">
    <div class="brand-lockup">
      <div class="brand-mark"></div>
      <p class="brand-name">Shine Fox<br>Auto Care</p>
    </div>
    <h2 class="services-title">Services Offered</h2>
    <p class="services-lead">Complete interior &amp; exterior detail</p>
    <div class="services-cols">
      <ul class="services-list">
        <li>Paint correction &amp; protection</li>
        <li>Auto carpet &amp; seat cleaning</li>
      </ul>
      <ul class="services-list">
        <li>Ceramic coating</li>
        <li>Trim restore</li>
      </ul>
    </div>
  </section>

</main>
</body>
</html>
```